Branding Pack for new business to business cost saving site

I would like a branding pack for my new project. I would like the following designed;
a4 Presentation folder
Letterhead
Envelope
Business Card
compliment splip

We are a business cost saving site, we have access to 1000s of discount offers for daily business to business offers. I already have the logo therfore please follow th e logo for the coloutr and design.

Target Market(s)

SMEs in United Kingdom

Industry/Entity Type

Business Service

Font styles to use
Serif
Script

Colors
0255a3
fbee3d

Requirements
Must have
• The folder needs to be the same size as attached

```html
<!DOCTYPE html>
<html lang="en">
<head>
<meta charset="utf-8">
<title>Spendmate Envelope Set</title>
<link href="https://fonts.googleapis.com/css2?family=Roboto:wght@400&display=swap" rel="stylesheet">
<style>
  :root {
    --navy: #333875;
    --yellow: #ecc94b;
    --paper: #f7f7f7;
    --silver: #e3e3e5;
    --backdrop: #cfcfd1;
  }
  html, body {
    margin: 0;
    padding: 0;
    width: 1200px;
    height: 991px;
    overflow: hidden;
    background: var(--backdrop);
  }
  .canvas {
    position: relative;
    width: 1200px;
    height: 991px;
  }
  .envelope {
    position: absolute;
    width: 761px;
    background: var(--paper);
    box-shadow: 0 1px 3px rgba(0,0,0,0.18);
    overflow: hidden;
  }
  .envelope--front { left: 217px; top: 82px; height: 382px; }
  .envelope--back { left: 220px; top: 526px; height: 383px; }
  .brand {
    position: absolute;
    display: flex;
    flex-direction: column;
    font-family: "Roboto", sans-serif;
    font-weight: 400;
    line-height: 1;
  }
  .brand__name { letter-spacing: 0.5px; }
  .brand__tagline {
    font-family: "Roboto", sans-serif;
    font-weight: 400;
    letter-spacing: 2.5px;
    margin-top: 4px;
  }
  .brand--front { left: 46px; top: 60px; color: var(--navy); }
  .brand--front .brand__name { font-size: 40px; }
  .brand--front .brand__tagline { font-size: 7px; }
  .brand--back { left: 50%; top: 44px; transform: translateX(-50%); color: #ffffff; align-items: center; }
  .brand--back .brand__name { font-size: 28px; }
  .brand--back .brand__tagline { font-size: 5px; letter-spacing: 2px; margin-top: 3px; }
  .return-address {
    position: absolute;
    left: 84px;
    top: 320px;
    margin: 0;
    width: 110px;
    text-align: center;
    font-family: "Roboto", sans-serif;
    font-size: 10px;
    line-height: 13px;
    color: var(--navy);
  }
  .base-band {
    position: absolute;
    left: 0;
    right: 0;
    bottom: 0;
    height: 22px;
    background: var(--navy);
    border-top: 2px solid var(--silver);
    box-shadow: 0 -4px 0 var(--yellow);
  }
  .flap { position: absolute; left: 0; top: 0; }
</style>
</head>
<body>
<div class="canvas">

  <section class="envelope envelope--front">
    <div class="brand brand--front">
      <span class="brand__name">spendmate</span>
      <span class="brand__tagline">SMART SAVINGS FOR FIRMS</span>
    </div>
    <p class="return-address">Level 2, 18 Harbour Rd.<br>Kingsport QLD 4821</p>
    <div class="base-band"></div>
  </section>

  <section class="envelope envelope--back">
    <svg class="flap" width="761" height="112" viewBox="0 0 761 112">
      <path d="M0,0 L761,0 L731,104 Q729,110 722,110 L39,110 Q32,110 30,104 Z" fill="var(--navy)"/>
    </svg>
    <div class="brand brand--back">
      <span class="brand__name">spendmate</span>
      <span class="brand__tagline">SMART SAVINGS FOR FIRMS</span>
    </div>
  </section>

</div>
</body>
</html>
```